KVR Inc Web Design

WHAT ARE WE DOING?
We are developing a new website look and feel for a new company called KVR Inc. This new look and feel should include colors, design elements, choice of photography and other imagery, fonts, and other user experience elements.

WHAT DO THEY DO?
KVR, Inc, makes tools for researchers who are studying protein-protein interactions. These molecules are the basic tools of biology, and serve as key targets for drug developers and disease researchers. The world of proteins is enormously complex, and companies like KVR provide researchers with critical tools that help them elucidate this world.

WHO ARE WE TALKING TO?
The target audience for this website are professional scientists working in university research or biopharma drug development. They are highly sophisticated consumers looking for key tools that will advance their research.

WHAT DO WE WANT THEM TO DO?
The site is an information resource for the customer exploring the tools that KVR sells and the scientific issues surrounding protein-protein interactions. They should be able to navigate easily to their content of choice, while the whole site should convey a professionalism that enhanced KVR’s credibility.

WHAT DOES THE KVR BRAND STAND FOR?
KVR stands for illumination. Proteins are challenging to study, and KVR exists to help shed light on their workings.

WHAT ARE THE KEY VALUES OF THE KVR BRAND?
Integrity. Innovation. Insight.

WHAT ARE THE EXECUTIONAL MANDITORIES?
The look and feel is completely up for grabs. Nothing is off the table.

WHAT ARE THE DELIVERABLES?
We need new designs for the following templates:
http://cms.marlowbench.com/
http://cms.marlowbench.com/products-and-services/instruments-3/bench-top-instruments/
http://cms.marlowbench.com/category/lab-study/

```html
<!DOCTYPE html>
<html lang="en">
<head>
<meta charset="utf-8">
<title>KVR Inc — Company</title>
<link rel="stylesheet" href="https://fonts.googleapis.com/css2?family=Mulish:wght@300;400;600;700&display=swap">
<style>
:root{
  --orange:#f8ad3a;
  --teal:#2fb3d6;
  --btn-teal:#2b8fae;
  --text:#555;
  --dark:#5f5f5f;
  --rule:#d6d6d6;
  --field:#eeeded;
  --footer:#6b6b6b;
}
*{box-sizing:border-box;margin:0;padding:0}
html,body{width:1106px;height:1200px;overflow:hidden;background:#fff}
body{font-family:"Mulish",sans-serif;color:var(--text)}
.page{position:relative;width:1280px;height:1389px;transform:scale(.86406);transform-origin:0 0}
.header{position:absolute;left:0;top:0;width:1280px;height:65px;border-top:3px solid var(--orange);border-bottom:1px solid #e6e6e6}
.brand{position:absolute;left:128px;top:14px;display:flex;align-items:center;gap:10px;font-weight:300;font-size:32px;letter-spacing:6px;color:#666}
.brand-dot{width:10px;height:10px;background:var(--orange)}
.nav{position:absolute;left:326px;top:21px;display:flex;gap:24px;font-weight:700;font-size:16px;color:var(--dark)}
.nav .active{color:var(--orange)}
.search{position:absolute;left:1005px;top:17px;width:147px;height:27px;background:#8c8c8c;color:#ddd;font-size:14px;padding:5px 8px}
.search svg{position:absolute;right:7px;top:6px}
.sidebar{position:absolute;left:127px;top:96px;width:236px}
.side-title{font-weight:700;font-size:19px;color:var(--teal);padding-bottom:10px;border-bottom:3px double var(--rule)}
.subnav{list-style:none;margin-bottom:42px}
.subnav li{height:36px;line-height:36px;border-bottom:1px solid #e6e6e6;font-size:17px;color:var(--dark);position:relative;padding-left:14px}
.subnav li:last-child{border-bottom:none}
.subnav li::before{content:"»";position:absolute;left:0;font-size:13px}
.subnav li.current{color:var(--orange)}
.subnav li.current svg{position:absolute;right:12px;top:14px}
.news-item{padding:26px 0 14px 1px;border-bottom:1px solid #e6e6e6;font-size:14px;line-height:18px;color:var(--dark)}
.news-item:last-of-type{border-bottom:none}
.news-date{font-style:italic;color:#aaa}
.btn-orange{display:block;width:135px;height:27px;margin-top:16px;background:var(--orange);color:#fff;text-align:center;line-height:27px;font-size:15px}
.main{position:absolute;left:390px;top:80px;width:762px}
.page-title{display:flex;align-items:center;gap:10px;font-size:30px;color:var(--dark);padding-bottom:6px;border-bottom:3px double var(--rule)}
.section-title{font-size:22px;color:var(--orange);margin:16px 0 14px}
.main p{font-size:14.5px;line-height:20px;margin-bottom:20px}
.main a{color:var(--orange);text-decoration:none}
.photo-frame{border:1px solid #ddd;padding:6px;margin-top:22px}
.photo{height:305px;background:linear-gradient(90deg,#cfd3d6 0%,#b8b2aa 40%,#e6e2dc 65%,#d8d4cf 100%)}
.contact-title{font-size:19px;color:var(--dark);margin-top:18px;padding-bottom:10px;width:682px;border-bottom:3px double var(--rule)}
.nature{width:682px;height:46px;border-bottom:3px double var(--rule);display:flex;align-items:center;font-size:14px;color:var(--dark)}
.radio{display:flex;align-items:center;gap:6px;width:136px}
.radio i{width:9px;height:9px;border-radius:50%;border:2px solid #bbb;background:#fff}
.radio.on i{border-color:#999;background:#557}
.nature .other-field{width:129px;height:28px;background:var(--field);border:1px solid #ddd;margin-left:-70px}
.form{margin-top:22px}
.row{display:flex;align-items:flex-start;margin-bottom:6px}
.row label{width:70px;text-align:right;font-size:14px;color:var(--dark);margin-right:16px;padding-top:8px}
.field{width:339px;height:29px;background:var(--field);border:1px solid #d8d8d8}
.field.white{background:#fff}
.field.tall{height:149px}
.btn-submit{margin:10px 0 0 289px;width:135px;height:27px;background:var(--btn-teal);color:#fff;font-weight:700;font-size:15px;text-align:center;line-height:27px}
.footer{position:absolute;left:0;top:1322px;width:1280px;height:67px;background:var(--footer);color:#fff;font-size:14px}
.footer-nav{position:absolute;left:128px;top:27px}
.social{position:absolute;left:879px;top:22px;display:flex;gap:6px}
.social span{width:26px;height:26px;border-radius:50%;background:#fff}
.copyright{position:absolute;left:991px;top:28px;font-size:15px}
.copyright em{font-style:normal;color:var(--orange)}
</style>
</head>
<body>
<div class="page">
  <header class="header">
    <div class="brand"><span class="brand-dot"></span>KVR INC</div>
    <nav class="nav">
      <span>Company</span><span class="active">Products &amp; Services</span><span>Learning Center</span><span>Events</span><span>KVR News</span><span>Contact</span>
    </nav>
    <div class="search">Search
      <svg width="14" height="14" viewBox="0 0 14 14"><circle cx="6" cy="6" r="4.5" fill="none" stroke="#ccc" stroke-width="1.5"/><path d="M9.5 9.5l3.5 3.5" stroke="#ccc" stroke-width="1.5"/></svg>
    </div>
  </header>

  <aside class="sidebar">
    <h2 class="side-title">Sub Navigation</h2>
    <ul class="subnav">
      <li>Overview</li>
      <li class="current">Locations<svg width="26" height="8" viewBox="0 0 26 8"><path d="M0 4h24M20 1l4 3-4 3" fill="none" stroke="#f8ad3a" stroke-width="1"/></svg></li>
      <li>Quality Leadership</li>
      <li>Community</li>
    </ul>
    <h2 class="side-title">Latest News</h2>
    <div class="news-item"><div class="news-date">October 17, 2013</div>Lorem ipsum dolor sit &nbsp;amet, consect etureius mod dipisi cing elit, sed do eiusmod tempor<br>Learn More &gt;&gt;&gt;</div>
    <div class="news-item"><div class="news-date">October 17, 2013</div>Lorem ipsum dolor sit &nbsp;amet, consect etureius mod dipisi cing elit, sed do eiusmod tempor<br>Learn More &gt;&gt;&gt;</div>
    <span class="btn-orange">Click Here</span>
  </aside>

  <main class="main">
    <h1 class="page-title">
      <svg width="26" height="42" viewBox="0 0 26 42"><circle cx="11" cy="3" r="2" fill="none" stroke="#666"/><path d="M9 10h8v10l8 18a2 2 0 0 1-2 3H3a2 2 0 0 1-2-3l8-18z" fill="none" stroke="#666" stroke-width="2"/><path d="M5 30h16l3 8H2z" fill="#666"/></svg>
      COMPANY
    </h1>
    <h2 class="section-title">Trust Your Results</h2>
    <p>Quisque feugiat lacus vitae posuere blandit. Nulla sit amet laoreet felis, id rhoncus nisi. Aenean fringilla quam in nibh egestas, in malesuada tortor accumsan. Donec non massa lacinia, commodo eros eget, rutrum arcu. Integer tincidunt, velit id eleifend congue, odio massa consequat mauris, a scelerisque nulla nulla eu nulla. Cras luctus pulvinar nibh ut viverra. Aenean vestibulum vitae justo non dictum. Mauris ut tellus in dui pretium dictum nec non tortor. Nulla a velit quis dolor interdum scelerisque eu et nisi.</p>
    <p>Donec auctor mollis ligula eget molestie. Aliquam erat volutpat. Curabitur sapien libero, condimentum ac nisi ultricies tincidunt ipsum. Donec in iaculis metus. Mauris eleifend nisi non sapien commodo, hendrerit consectetur. Pellentesque faucibus, purus non dictum lacinia, ante augue pretium neque, vitae egestas dui nisi et enim. ornare Suspendisse nibh vel lacinia rhoncus Donec auctor mollis ligula eget molestie. Pellentesque faucibus, purus non dictum lacinia, ante augue pretium neque, <a href="#">vitae egestas</a> dui nisi et enim. Suspendisse iaculis nibh vel lacinia rhoncus</p>
    <div class="photo-frame"><div class="photo" role="img" aria-label="Scientists in lab coats working beside flasks of coloured liquid"></div></div>

    <h2 class="section-title" style="margin-top:24px">Submit a Message</h2>
    <p>Consectetuer adipiscing elit. Aenean commodo ligula eget dolor. Aenean massa. Cum sociis natoque penatibus et magnis dis parturient montes, nascetur ridiculus mus.</p>
    <h3 class="contact-title">Nature of Contact</h3>
    <div class="nature">
      <span class="radio on"><i></i>Products</span>
      <span class="radio"><i></i>Services</span>
      <span class="radio"><i></i>Support</span>
      <span class="radio"><i></i>Other</span>
      <span class="other-field"></span>
    </div>
    <div class="form">
      <div class="row"><label>First Name</label><div class="field"></div></div>
      <div class="row"><label>Last Name</label><div class="field white"></div></div>
      <div class="row"><label>Email ID</label><div class="field"></div></div>
      <div class="row"><label>Message</label><div class="field tall"></div></div>
      <div class="btn-submit">Submit Now</div>
    </div>
  </main>

  <footer class="footer">
    <div class="footer-nav">Company &nbsp;- &nbsp;Products &amp; Services &nbsp;- &nbsp;Learning Center &nbsp;- &nbsp;Events &nbsp;- &nbsp;KVR News &nbsp;- &nbsp;Contact</div>
    <div class="social"><span></span><span></span><span></span></div>
    <div class="copyright">Copyright © <em>KVR Inc.</em> 2013</div>
  </footer>
</div>
</body>
</html>
```